Company brochure for our unique consulting business

We are a small consulting business offering a unique set of services to our clients.. In simple terms we are a business improvement consultancy helping our clients get the best out of their businesses. We work with clients across multiple sectors and deliver a variety of services. We want to put together a brochure to cover these main themes:1. Who we are2. What we do3. The type of people we employ4. The sectors we work inWhile the brochure needs to have a certain corporate feel to it, we don't want it to be "boring" or "stiff". We would like it to have a slightly "friendly" or "informal" feel to it, to reflect the type of organisation we are.We have a company website http://brevalconsultingpartners.net , however we do not want to directly replicate the content or feel as we recognise it needs updating.We would like the brochure to be A4 portrait format. We anticipate requiring 12 sides (including covers) but we are happy to be guided on this based on the content we have provided.The attached ppt file gives the detail of the content to be included and also shows the proposed pagination. For the front cover we would like to try 2 versions, one with the BCP logo and one with the Breval Consulting Partners logo (a file of both is attached)One of the most important pages will be the "Our Services" page. We would like this to cover the centre fold. In the ppt file we have shown an example layout, but this is where we need most help - we are clearly not graphic designers! This page will be the most used page in sales meetings etc.Also attached is the following:1. file for our BrevalConsulting Partners company logo.2. File for our BCP company logo3. Files for Derek's signatures (for under photos) - Owen's to follow4. Photo of Derek & Owen (person in purple shirt to be cropped out)Thank you and really excited to see what everyone comes back with.Derek & Owen

Target Market(s)

Very broad - Manufacturing, Healthcare, Hospitality

Industry/Entity Type

Management Consulting

Font styles to use
Other font styles liked:
• We use Swiss721, but happy to be guided by designer

Colors
3276b5
85abd2
0355a3
333333
5c5c5c
9d9d9d
d9d9d9

Requirements
Must have
• Corporate feel
Nice to have
• Slightly friendly feel
• Our standard "blue" is (CORRECTION) - R55 G96 B146 #376092 and our standard grey is R197 G178, B179 - #B3B2B2, which we would like to keep, but other colours we are happy to be guided on. Brand guidelines attached.

```html
<!DOCTYPE html>
<html lang="en">
<head>
<meta charset="utf-8">
<title>BCP – Contact us</title>
<link href="https://fonts.googleapis.com/css2?family=Noto+Sans:wght@400;700&display=swap" rel="stylesheet">
<style>
  :root {
    --sky-light: #dbeaf7;
    --sky-mid: #8fb8e0;
    --sky-deep: #3c6fae;
    --navy: #0f1d52;
    --band-blue: #2a50cf;
    --accent-blue: #2a5bd0;
    --ink: #111111;
    --paper: #ffffff;
  }
  html, body {
    margin: 0;
    padding: 0;
    overflow: hidden;
    background: var(--paper);
  }
  .back-cover {
    position: relative;
    width: 848px;
    height: 1200px;
    overflow: hidden;
    font-family: "Noto Sans", Verdana, sans-serif;
    color: var(--ink);
  }
  .cover-shapes {
    position: absolute;
    inset: 0;
  }
  .contact-block {
    position: absolute;
    left: 452px;
    top: 690px;
    transform: rotate(-16deg);
    transform-origin: left top;
    white-space: nowrap;
  }
  .brand-name {
    display: flex;
    align-items: center;
    gap: 8px;
    font-weight: 700;
    font-size: 40px;
    line-height: 44px;
    letter-spacing: 1px;
    color: var(--ink);
  }
  .brand-square {
    width: 16px;
    height: 16px;
    background: var(--accent-blue);
  }
  .contact-heading {
    margin: 6px 0 0 14px;
    font-weight: 400;
    font-size: 22px;
    line-height: 30px;
    color: var(--accent-blue);
  }
  .postal-address {
    margin: 68px 0 0 0;
    font-style: normal;
    font-size: 16px;
    line-height: 30px;
  }
  .direct-lines {
    margin: 18px 0 0 0;
    font-size: 16px;
    line-height: 28px;
  }
  .direct-lines p, .postal-address p { margin: 0; }
</style>
</head>
<body>
<main class="back-cover">
  <svg class="cover-shapes" width="848" height="1200" viewBox="0 0 848 1200" xmlns="http://www.w3.org/2000/svg">
    <defs>
      <linearGradient id="skyGradient" x1="0" y1="0" x2="1" y2="1">
        <stop offset="0" stop-color="#5f8fc7"/>
        <stop offset="0.45" stop-color="#cfe2f4"/>
        <stop offset="0.75" stop-color="#8fb8e0"/>
        <stop offset="1" stop-color="#3c6fae"/>
      </linearGradient>
    </defs>
    <rect class="cityscape-photo" x="0" y="0" width="848" height="620" fill="url(#skyGradient)" role="img" aria-label="Upward view of glass office towers against a blue sky"/>
    <polygon class="navy-panel" points="0,590 336,476 552,1200 0,1200" fill="var(--navy)"/>
    <polygon class="accent-band" points="232,478 304,454 524,1200 448,1200" fill="var(--band-blue)"/>
    <polygon class="white-panel" points="336,476 848,308 848,1200 552,1200" fill="var(--paper)"/>
  </svg>

  <section class="contact-block">
    <div class="brand-name"><span class="brand-square"></span>BCP</div>
    <h2 class="contact-heading">Contact us</h2>
    <address class="postal-address">
      <p>BCP Limited</p>
      <p>Kingsmead House</p>
      <p>Calder Lane</p>
      <p>Ashford</p>
      <p>AF2 7QL</p>
    </address>
    <div class="direct-lines">
      <p>Tel: +44 (0) 1632 960214</p>
      <p>hello@brevalgroup.net</p>
      <p>www.brevalgroup.net</p>
    </div>
  </section>
</main>
</body>
</html>
```